KAJU Freightways #ALLKAJU Business Cards & Letterhead

I am looking to business cards designed for our organization. We are currently undergoing a small re-branding that is taking place. Our organization is called KAJU Freightways and we are headquartered in Phoenix, AZ. We primarily provide transportation and logistics services to the Marlow Parcel Bureau who is our largest customer. I would like to see a design that incorporates name, title, contact info, website, and address (this will be different depending on the employee). I would also like to see some color on the business card using our logo colors or a variation. I would like our logo on the back of the business card with the website displayed. The final design should communicate that we are a next generation transportation operate that focuses on being driver-first, customer-centric, innovative, and sustainable.We would also like our #ALLKAJU catch phrase incorporated as well.

Target Market(s)

Transportation & Logistics

Industry/Entity Type

Trucking Company

Contact Information for Business Card

-First and Last Name
-Position Title
-Contact Phone
-Contact Email
-Physical Address

Font styles to use
Serif

Colors

Designer to choose colors to be used in the design.

Requirements
Must have
• -KAJU logo prominently displayed
• -#ALLKAJU catch phrase used
• -Some amount of color, design gradient, etc.
• -Logo on the back with website listed (https://www.kajufreightco.example)

```html
<!DOCTYPE html>
<html lang="en">
<head>
<meta charset="utf-8">
<title>KAJU Freightways Business Card</title>
<link rel="stylesheet" href="https://fonts.googleapis.com/css2?family=Roboto+Serif:opsz,wdth,wght@8..144,50..150,400..800&family=Roboto:wght@400;700;900&display=swap">
<style>
  :root {
    --stage: #e1e1df;
    --card-dark: #0b0c0e;
    --pattern-tone: #15171a;
    --card-light: #fdfdfd;
    --navy: #0b3d4a;
    --green: #7dc52e;
    --white: #ffffff;
    --muted: #9a9ea3;
  }
  * { margin: 0; padding: 0; box-sizing: border-box; }
  html, body { width: 1200px; height: 828px; overflow: hidden; }
  body {
    background: var(--stage);
    font-family: "Roboto", Arial, sans-serif;
    position: relative;
  }
  .card {
    position: absolute;
    top: 102px;
    width: 377px;
    height: 623px;
  }
  .card-back { left: 194px; background: var(--card-dark); overflow: hidden; }
  .card-front { left: 628px; background: var(--card-light); color: var(--navy); }

  .back-pattern {
    position: absolute; inset: 0;
    background: radial-gradient(circle at 50% 50%, var(--pattern-tone), var(--card-dark) 80%);
  }
  .back-mark {
    position: absolute;
    left: 249px; top: 405px;
    width: 68px; height: 68px;
    border: 2.5px solid var(--green);
    border-radius: 50%;
    display: flex; align-items: center; justify-content: center;
    color: var(--white);
    font-weight: 900;
    font-size: 18px;
    letter-spacing: 0.5px;
  }
  .back-footer {
    position: absolute;
    left: 0; bottom: 34px; width: 100%;
    text-align: center;
    font-family: "Roboto Serif", Georgia, serif;
  }
  .back-tagline { font-size: 18px; font-weight: 700; color: var(--green); letter-spacing: 1px; }
  .back-website { margin-top: 6px; font-size: 13px; color: var(--muted); }

  .brand-mark {
    position: absolute;
    left: 75px; top: 53px;
    width: 228px; height: 228px;
    border: 5px solid var(--green);
    border-radius: 50%;
    display: flex; align-items: center; justify-content: center;
    font-weight: 900;
    font-size: 70px;
    letter-spacing: 1px;
    color: var(--navy);
  }
  .centered { position: absolute; left: 0; width: 100%; text-align: center; }
  .person-name {
    top: 322px;
    font-family: "Roboto Serif", Georgia, serif;
    font-stretch: 75%;
    font-weight: 700;
    font-size: 27px;
    line-height: 32px;
  }
  .person-title { top: 356px; font-size: 17px; color: var(--green); }
  .divider { top: 404px; height: 18px; display: flex; justify-content: center; align-items: center; gap: 9px; }
  .divider .rule { width: 56px; height: 1.5px; background: var(--green); }
  .divider .rule:first-child { margin-right: 14px; }
  .divider .rule:last-child { margin-left: 14px; }
  .divider svg { width: 15px; height: 15px; fill: var(--green); }
  .contact-list { top: 434px; font-size: 17px; line-height: 24px; }
  .company-name { top: 516px; font-size: 17px; font-weight: 700; color: var(--green); }
  .company-address { top: 541px; font-size: 17px; line-height: 24px; }
</style>
</head>
<body>
  <section class="card card-back">
    <div class="back-pattern" role="img" aria-label="Repeating faint brand-name pattern on black"></div>
    <div class="back-mark">KAJU</div>
    <div class="back-footer">
      <p class="back-tagline">#ALLKAJU</p>
      <p class="back-website">https://www.kajufreightco.example</p>
    </div>
  </section>

  <section class="card card-front">
    <div class="brand-mark">KAJU</div>
    <h1 class="centered person-name">Dorian Whitfield</h1>
    <p class="centered person-title">Chairman &amp; CEO</p>

    <div class="centered divider">
      <span class="rule"></span>
      <svg viewBox="0 0 16 16" aria-label="Phone"><path d="M2 6c0-2 2.5-3 6-3s6 1 6 3v1h-3V5.8C10 5.4 9 5.3 8 5.3s-2 .1-3 .5V7H2zM4 8h8l2 5H2zm4 1.3a1.5 1.5 0 1 0 0 3 1.5 1.5 0 0 0 0-3z"/></svg>
      <svg viewBox="0 0 16 16" aria-label="Email"><path d="M1 3h14v10H1zm1.5 1.3v.3L8 8.6l5.5-4v-.3zM2.5 6.2v5.5h11V6.2L8 10.2z"/></svg>
      <svg viewBox="0 0 16 16" aria-label="Website"><path d="M8 1a7 7 0 1 0 0 14A7 7 0 0 0 8 1zm0 1.4c.8 0 1.7 1.5 2 4h-4c.3-2.5 1.2-4 2-4zm-2.1.4C5.3 3.8 5 5 4.8 6.4H2.6a5.7 5.7 0 0 1 3.3-3.6zm4.2 0a5.7 5.7 0 0 1 3.3 3.6h-2.2c-.2-1.4-.5-2.6-1.1-3.6zM2.4 7.6h2.3v.8l.1 1H2.6a5.6 5.6 0 0 1-.2-1.8zm3.5 0h4.2v.8l-.1 1H6l-.1-1zm5.4 0h2.3c0 .6-.1 1.2-.2 1.8h-2.2l.1-1zM2.9 10.6h2.1c.2 1.1.5 2 .9 2.6a5.7 5.7 0 0 1-3-2.6zm3.3 0h3.6c-.4 1.8-1.1 3-1.8 3s-1.4-1.2-1.8-3zm4.8 0h2.1a5.7 5.7 0 0 1-3 2.6c.4-.6.7-1.5.9-2.6z"/></svg>
      <span class="rule"></span>
    </div>

    <p class="centered contact-list">602-555-0148<br>dorian@kajufreightco.example<br>www.kajufreightco.example</p>
    <p class="centered company-name">KAJU Freightways &amp; Energy Services</p>
    <p class="centered company-address">4120 North Canyon Ridge<br>Parkway Phoenix, AZ 85027</p>
  </section>
</body>
</html>
```